We need a complete design for our construction company KELTO CONSTRUCTION based in Auckland New Zealand, we need a logo, website, business card, vehicle design etc..
We are a mid to high-end construction company who work mostly on residential projects and some commercial.

What we want to see in the design;
Professional,
Architectural,
Simple,
Alternative,

We want the design to communicate professionalism, high quality wormanship and and quality service.

Target Market(s)

People looking for a quality building/ construction company

Industry/Entity Type

Construction Company

Contact Information for Business Card

KELTO CONSTRUCTION.co.nz
Lino Verasek
lino@keltoconstruction.example.nz
021 5807 462

Logo Text

KELTO CONSTRUCTION

Number of Pages Required

5+ page

Font styles to use
Sans Serif

Colors

Designer to choose colors to be used in the design.

Requirements
Must have
• Must appear high end, professional, quality, be simple, easy to use, give security to potential clients
Nice to have
• high-quality photos of our recent projects
• about us page
• blog page
• contact us page
• high quality content
Should not have
• should not be hard to use and have too much going on.

```html
<!DOCTYPE html>
<html lang="en">
<head>
<meta charset="utf-8">
<title>Kelto Construction</title>
<link rel="stylesheet" href="https://fonts.googleapis.com/css2?family=Roboto:ital,wght@0,400;0,500;0,700;1,400&display=swap">
<style>
:root{
  --pink:#f5155f;
  --yellow:#f6c117;
  --dark:#2b2b2b;
  --text:#333;
  --muted:#555;
  --light:#efefef;
  --white:#fff;
  --footer-brand:#9a9a9a;
}
*{margin:0;padding:0;box-sizing:border-box}
html,body{width:1200px;height:2980px;overflow:hidden}
body{position:relative;font-family:Roboto,Arial,sans-serif;color:var(--text);background:var(--white)}
.abs{position:absolute}
.brand{display:flex;align-items:center;gap:10px;font-weight:700;font-size:22px;letter-spacing:.5px;color:var(--dark);line-height:1}
.brand-mark{width:14px;height:14px;background:var(--pink);display:block}
.nav{left:405px;top:40px;display:flex;gap:34px;font-size:14px;font-weight:500;color:#222}
.nav .on{color:var(--pink)}
.call{left:856px;top:32px;width:270px;height:36px;background:var(--yellow);color:#222;font-weight:700;font-size:17px;display:flex;align-items:center;justify-content:center;gap:8px}
.hero{left:0;top:96px;width:1200px;height:568px;background:linear-gradient(180deg,#2f5f9c 0%,#6c8fb9 45%,#4a5563 75%,#2b3a55 100%)}
.hero-title{left:0;top:272px;width:1200px;text-align:center;color:#fff;font-size:56px;font-weight:700;letter-spacing:1px}
.hero-sub{left:280px;top:346px;width:640px;text-align:center;color:var(--yellow);font-size:20px;font-weight:700;line-height:28px}
.btn{display:flex;align-items:center;justify-content:center;font-size:14px;font-weight:700;text-transform:uppercase}
.btn-pink{background:var(--pink);color:#fff}
.btn-yellow{background:var(--yellow);color:#222}
.arrow-circle{width:42px;height:42px;border:2px solid rgba(255,255,255,.8);border-radius:50%}
.welcome{left:0;top:664px;width:1200px;height:336px;background:linear-gradient(180deg,#fff 30%,#f0f0f0 100%)}
.h-small{left:0;width:1200px;text-align:center;font-size:23px;font-weight:500;color:#222}
.h-pink{left:0;width:1200px;text-align:center;font-size:28px;font-weight:700;color:var(--pink)}
.intro{left:78px;top:790px;width:1044px;text-align:center;font-size:14.5px;line-height:28px;color:var(--muted)}
.tile{display:flex;flex-direction:column;align-items:center;justify-content:center;text-align:center;color:#fff;padding:0 40px}
.tile h3{font-size:23px;font-weight:500;letter-spacing:.5px}
.tile hr{width:64px;border:0;border-top:3px solid #fff;margin:14px 0 20px}
.tile p{font-size:14.5px;line-height:27px}
.t-pink{background:var(--pink)}
.t-yellow{background:var(--yellow)}
.t-dark{background:var(--dark)}
.recent{left:0;top:1766px;width:1200px;height:644px;background:var(--light)}
.sec-title{left:0;width:1200px;text-align:center;font-size:23px;font-weight:700;color:#222}
.rule{width:64px;height:3px;background:var(--pink)}
.quote{width:300px;text-align:center;font-style:italic;font-size:14.5px;line-height:28px;color:var(--muted)}
.who{width:300px;text-align:center;font-size:14.5px;font-weight:700;color:var(--yellow)}
.where{width:300px;text-align:center;font-size:12px;color:var(--pink)}
.footer{left:0;top:2742px;width:1200px;height:238px;background:var(--dark)}
.f-brand{font-weight:700;color:var(--footer-brand);font-size:20px;letter-spacing:.5px;line-height:1}
.f-copy{font-size:11.5px;line-height:22px;color:#bbb}
.f-head{font-size:14px;font-weight:700;color:var(--yellow)}
.f-list{font-size:13px;line-height:28px;color:#ddd;list-style:none}
.f-text{font-size:13px;line-height:22px;color:#ddd}
.social{display:flex;gap:20px}
.social span{width:22px;height:22px;border-radius:50%;background:#bbb;display:block}
</style>
</head>
<body>

<header>
  <div class="abs brand" style="left:76px;top:39px"><span class="brand-mark"></span>KELTO CONSTRUCTION</div>
  <nav class="abs nav"><span class="on">HOME</span><span>ABOUT</span><span>PROJECTS</span><span>BLOG</span><span>CONTACT US</span></nav>
  <div class="abs call">
    <svg width="16" height="16" viewBox="0 0 24 24"><path fill="#222" d="M6.6 10.8c1.4 2.8 3.8 5.1 6.6 6.6l2.2-2.2c.3-.3.7-.4 1-.2 1.1.4 2.3.6 3.6.6.6 0 1 .4 1 1V20c0 .6-.4 1-1 1C10.6 21 3 13.4 3 4c0-.6.4-1 1-1h3.5c.6 0 1 .4 1 1 0 1.3.2 2.5.6 3.6.1.3 0 .7-.2 1z"/></svg>
    CALL US: 09-555-0147
  </div>
</header>

<section>
  <div class="abs hero" role="img" aria-label="City skyline with harbour and tower under a blue sky"></div>
  <div class="abs arrow-circle" style="left:60px;top:360px"><svg width="38" height="38" viewBox="0 0 38 38"><path d="M22 12l-7 7 7 7" stroke="#fff" stroke-width="2" fill="none"/></svg></div>
  <div class="abs arrow-circle" style="left:1098px;top:360px"><svg width="38" height="38" viewBox="0 0 38 38"><path d="M16 12l7 7-7 7" stroke="#fff" stroke-width="2" fill="none"/></svg></div>
  <h1 class="abs hero-title">KELTO CONSTRUCTION</h1>
  <p class="abs hero-sub">Vestibulum ante ipsum primis in faucibus orci luctus et ultrices posuere cubilia..</p>
  <div class="abs btn btn-pink" style="left:512px;top:424px;width:178px;height:46px">CONTACT US</div>
</section>

<section>
  <div class="abs welcome"></div>
  <h2 class="abs h-small" style="top:713px">WELCOME TO</h2>
  <h2 class="abs h-pink" style="top:740px">KELTO CONSTRUCTION</h2>
  <p class="abs intro">Aliquam molestie, mi et imperdiet euismod, dui purus auctor tellus, et interdum lacus lectus et ante. Sed accumsan sollicitudin sapien, sit amet adipiscing turpis gravida ac. In congue, neque ac lobortis volutpat, libero mauris varius mi, vitae suscipit ipsum ligula vitae risus. Duis aliquam nibh a dui iaculis viverra id a velit. Vivamus egestas risus in magna varius commodo. Sed semper viverra egestas.</p>
  <div class="abs btn btn-yellow" style="left:512px;top:900px;width:178px;height:46px">READ MORE</div>
</section>

<section>
  <div class="abs tile t-pink" style="left:76px;top:1014px;width:420px;height:224px"><h3>RESIDENTIAL PROJECTS</h3><hr><p>Aliquam molestie, mi et imperdiet euismod, dui purus auctor tellus, et interdum lacus lectus..</p></div>
  <div class="abs" style="left:512px;top:1014px;width:300px;height:224px;background:linear-gradient(170deg,#b7c6d6,#a06b4e)" role="img" aria-label="Brick house under construction with scaffolding"></div>
  <div class="abs" style="left:826px;top:1014px;width:300px;height:224px;background:linear-gradient(160deg,#6d5a49,#3f5f8a)" role="img" aria-label="Builders reviewing plans on site"></div>

  <div class="abs" style="left:76px;top:1252px;width:300px;height:224px;background:linear-gradient(170deg,#c9d6e2,#8f9aa4)" role="img" aria-label="Modern office building with glass facade"></div>
  <div class="abs" style="left:390px;top:1252px;width:300px;height:224px;background:linear-gradient(180deg,#3e7fd0,#c7ccd2 60%,#7a7f86)" role="img" aria-label="Commercial warehouse building under blue sky"></div>
  <div class="abs tile t-yellow" style="left:704px;top:1252px;width:422px;height:224px"><h3>COMMERCIAL PROJECTS</h3><hr><p>Aliquam molestie, mi et imperdiet euismod, dui purus auctor tellus, et interdum lacus lectus..</p></div>

  <div class="abs tile t-dark" style="left:76px;top:1492px;width:420px;height:224px"><h3>HIGH-END CONSTRUCTION</h3><hr><p>Aliquam molestie, mi et imperdiet euismod, dui purus auctor tellus, et interdum lacus lectus..</p></div>
  <div class="abs" style="left:512px;top:1492px;width:300px;height:224px;background:linear-gradient(150deg,#1a3f86,#5f8fcf 50%,#14264f)" role="img" aria-label="Glass skyscrapers seen from below"></div>
  <div class="abs" style="left:826px;top:1492px;width:300px;height:224px;background:linear-gradient(180deg,#9fbddc,#b9b3aa 55%,#8c7b66)" role="img" aria-label="Concrete building frame under construction"></div>
</section>

<section>
  <div class="abs recent"></div>
  <h2 class="abs sec-title" style="top:1812px">OUR RECENT PROJECTS</h2>
  <div class="abs rule" style="left:568px;top:1848px"></div>
  <div class="abs" style="left:76px;top:1892px;width:252px;height:188px;background:linear-gradient(170deg,#a9c3df,#8a6a4f)" role="img" aria-label="Timber frame house under construction"></div>
  <div class="abs" style="left:342px;top:1892px;width:252px;height:188px;background:linear-gradient(170deg,#3f78c6,#6d5d52)" role="img" aria-label="Multi storey building with cranes"></div>
  <div class="abs" style="left:608px;top:1892px;width:252px;height:188px;background:linear-gradient(170deg,#7ea8d6,#b0a89b)" role="img" aria-label="Apartment block with scaffolding"></div>
  <div class="abs" style="left:874px;top:1892px;width:252px;height:188px;background:linear-gradient(170deg,#5a8fd0,#8c8780)" role="img" aria-label="House with steel roof framing"></div>
  <div class="abs" style="left:76px;top:2094px;width:252px;height:188px;background:linear-gradient(170deg,#a6c0dc,#9d9790)" role="img" aria-label="Concrete house shell with roof trusses"></div>
  <div class="abs" style="left:342px;top:2094px;width:252px;height:188px;background:linear-gradient(170deg,#c9a27a,#5e4a40)" role="img" aria-label="Tower cranes over brick building at sunset"></div>
  <div class="abs" style="left:608px;top:2094px;width:252px;height:188px;background:linear-gradient(170deg,#2d5aa0,#7c9ac0)" role="img" aria-label="Curved glass office tower"></div>
  <div class="abs" style="left:874px;top:2094px;width:252px;height:188px;background:linear-gradient(170deg,#c4d3e2,#a25f3e)" role="img" aria-label="Brick house with scaffolding"></div>
  <div class="abs btn btn-yellow" style="left:512px;top:2316px;width:178px;height:46px">VIEW ALL PROJECTS</div>
</section>

<section>
  <h2 class="abs sec-title" style="top:2458px">TESTIMONIALS</h2>
  <div class="abs rule" style="left:568px;top:2494px"></div>
  <svg class="abs" style="left:44px;top:2562px" width="20" height="26" viewBox="0 0 20 26"><path d="M15 3L5 13l10 10" stroke="#444" stroke-width="3" fill="none"/></svg>
  <svg class="abs" style="left:1136px;top:2562px" width="20" height="26" viewBox="0 0 20 26"><path d="M5 3l10 10L5 23" stroke="#444" stroke-width="3" fill="none"/></svg>

  <p class="abs quote" style="left:90px;top:2527px">" Aliquam molestie, mi et imperdiet euismod, dui purus auctor tellus, et interdum lacus lectus et ante. Sed accumsan sollicitudin sapien, sit amet adipiscing turpis gravida ac..."</p>
  <p class="abs who" style="left:90px;top:2650px">Mara Tennison</p>
  <p class="abs where" style="left:90px;top:2676px">Location</p>

  <p class="abs quote" style="left:450px;top:2527px">" Aliquam molestie, mi et imperdiet euismod, dui purus auctor tellus, et interdum lacus lectus et ante. Sed accumsan sollicitudin sapien, sit amet adipiscing turpis gravida ac..."</p>
  <p class="abs who" style="left:450px;top:2650px">Mara Tennison</p>
  <p class="abs where" style="left:450px;top:2676px">Location</p>

  <p class="abs quote" style="left:810px;top:2527px">" Aliquam molestie, mi et imperdiet euismod, dui purus auctor tellus, et interdum lacus lectus et ante. Sed accumsan sollicitudin sapien, sit amet adipiscing turpis gravida ac..."</p>
  <p class="abs who" style="left:810px;top:2650px">Mara Tennison</p>
  <p class="abs where" style="left:810px;top:2676px">Location</p>
</section>

<footer>
  <div class="abs footer"></div>
  <div class="abs f-brand" style="left:76px;top:2816px">KELTO CONSTRUCTION</div>
  <p class="abs f-copy" style="left:76px;top:2872px">Copyright © 2018. Kelto Construction<br>All Rights Reserved</p>

  <h4 class="abs f-head" style="left:368px;top:2782px">NAVIGATION</h4>
  <ul class="abs f-list" style="left:368px;top:2810px"><li>Home</li><li>About us</li><li>Projects</li><li>Blog</li><li>Contact Us</li></ul>

  <h4 class="abs f-head" style="left:608px;top:2782px">CONTACT US</h4>
  <p class="abs f-text" style="left:608px;top:2812px"><span style="color:var(--pink);font-weight:700;font-size:12px">KELTO CONSTRUCTION</span><br>42 Harbourview Lane,<br>Auckland 1010</p>
  <svg class="abs" style="left:608px;top:2888px" width="14" height="14" viewBox="0 0 24 24"><path fill="#ddd" d="M6.6 10.8c1.4 2.8 3.8 5.1 6.6 6.6l2.2-2.2c.3-.3.7-.4 1-.2 1.1.4 2.3.6 3.6.6.6 0 1 .4 1 1V20c0 .6-.4 1-1 1C10.6 21 3 13.4 3 4c0-.6.4-1 1-1h3.5c.6 0 1 .4 1 1 0 1.3.2 2.5.6 3.6.1.3 0 .7-.2 1z"/></svg>
  <p class="abs f-text" style="left:640px;top:2884px">09-555-0147</p>
  <svg class="abs" style="left:608px;top:2918px" width="14" height="12" viewBox="0 0 14 12"><rect x="0" y="0" width="14" height="12" fill="#ddd"/><path d="M0 0l7 6 7-6" stroke="#2b2b2b" stroke-width="1.5" fill="none"/></svg>
  <p class="abs f-text" style="left:640px;top:2912px">hello@keltoconstruction.example.nz</p>

  <h4 class="abs f-head" style="left:890px;top:2782px">FOLLOW US</h4>
  <div class="abs social" style="left:890px;top:2822px"><span></span><span></span><span></span><span></span><span></span></div>
</footer>

</body>
</html>
```